Clear Plastic Card Design

I am looking to have a business card designed from my logo icon. I am looking to match the style of a different business card I have attached in the files.
Looking for a card that is plastic, with layers of transparency in the shape of my logo icon (also attached in the files) - not a circle like the other card. The winning design will incorporate the red icon logo on the front and back and include the charity's name, "Light for the Weary Souls" in the same or similar font, as well as an email and phone number. For now, use the email: email@lightfortheweary-mail.org and the phone number 555-382-7194.
We like how the sample business card has transparency, partial and full opacity layers and a matching color scheme. Files will need to be in vector so that our business card printing company can work with it.
UPDATE:
We've some excellent designs in, thank you everyone! I got an early review from the owner, and he requested a minor redirect to find his perfect design. He wants the design to stand out by NOT being a rectangle. Try instead a circle, square, or best yet - something that falls in the outline of the logo icon, either fully or partially. Thank you, everyone!
Light for the Weary Souls text should be incorporated as well as a phone and email.

```html
<!DOCTYPE html>
<html lang="en">
<head>
<meta charset="utf-8">
<title>Light for the Weary Souls — Business Card</title>
<link href="https://fonts.googleapis.com/css2?family=Bebas+Neue&family=Poppins:wght@300&display=swap" rel="stylesheet">
<style>
  :root {
    --backdrop: #2b2b2b;
    --card-red: #d91f14;
    --tab-orange: #e8501a;
    --card-white: #ececea;
    --ink-white: #ffffff;
    --ink-dark: #1c1c1c;
    --accent-orange: #ee5a12;
  }
  * { margin: 0; padding: 0; box-sizing: border-box; }
  html, body {
    width: 1200px; height: 800px; overflow: hidden;
    background: var(--backdrop);
  }
  .stage {
    width: 1200px; height: 800px;
    display: flex; align-items: center; justify-content: center; gap: 70px;
  }
  /* Die-cut card: raised tab on top of a rounded body */
  .card {
    position: relative;
    width: 340px; height: 620px;
  }
  .card-tab {
    position: absolute; top: 0; left: 0;
    width: 250px; height: 172px;
    border-radius: 18px 18px 0 0;
    padding: 22px 18px 0;
    font-family: "Bebas Neue", sans-serif;
    font-size: 44px; line-height: 0.98; letter-spacing: 0.5px;
  }
  .card-body {
    position: absolute; left: 0; right: 0; top: 150px; bottom: 0;
    border-radius: 0 18px 18px 18px;
  }
  /* Front */
  .card-front .card-tab { background: var(--tab-orange); color: var(--ink-white); }
  .card-front .card-body { background: var(--card-red); color: var(--ink-white); }
  .contact-list {
    position: absolute; left: 28px; right: 16px; top: 60px;
    list-style: none;
    font-family: "Bebas Neue", sans-serif;
  }
  .contact-item { display: flex; align-items: center; gap: 12px; margin-bottom: 14px; }
  .contact-icon {
    width: 30px; height: 30px; border-radius: 50%;
    background: var(--ink-white);
    display: flex; align-items: center; justify-content: center; flex-shrink: 0;
  }
  .contact-phone { font-size: 34px; letter-spacing: 1px; }
  .contact-email { font-size: 19px; letter-spacing: 0.4px; white-space: nowrap; }
  .name-box {
    position: absolute; left: 28px; right: 28px; bottom: 34px;
    border: 2px solid var(--ink-white); border-radius: 10px;
    padding: 16px 12px 12px;
    font-family: "Bebas Neue", sans-serif;
    text-align: center; line-height: 0.92;
  }
  .name-box-top { display: block; font-size: 54px; }
  .name-box-bottom { display: block; font-size: 42px; }
  /* Back */
  .card-back .card-tab { background: var(--card-white); color: var(--card-red); }
  .card-back .card-body { background: var(--card-white); color: var(--ink-dark); }
  .back-signature {
    position: absolute; right: 28px; bottom: 36px;
    display: flex; align-items: center; gap: 10px;
    font-family: "Poppins", sans-serif; font-weight: 300;
    font-size: 17px; line-height: 1.2; text-align: right;
    color: var(--ink-dark);
  }
  .signature-dot {
    width: 22px; height: 22px; border-radius: 50%;
    background: var(--accent-orange); flex-shrink: 0;
  }
</style>
</head>
<body>
<main class="stage">
  <section class="card card-front" aria-label="Card front">
    <div class="card-body">
      <ul class="contact-list">
        <li class="contact-item">
          <span class="contact-icon">
            <svg width="16" height="16" viewBox="0 0 24 24" aria-hidden="true">
              <path fill="#d91f14" d="M6.6 10.8a15.1 15.1 0 0 0 6.6 6.6l2.2-2.2a1 1 0 0 1 1-.25 11.4 11.4 0 0 0 3.6.57 1 1 0 0 1 1 1V20a1 1 0 0 1-1 1A17 17 0 0 1 3 4a1 1 0 0 1 1-1h3.5a1 1 0 0 1 1 1c0 1.25.2 2.45.57 3.57a1 1 0 0 1-.25 1z"/>
            </svg>
          </span>
          <span class="contact-phone">555-382-7194</span>
        </li>
        <li class="contact-item">
          <span class="contact-icon">
            <svg width="16" height="16" viewBox="0 0 24 24" aria-hidden="true">
              <path fill="#d91f14" d="M2 21l21-9L2 3v7l15 2-15 2z"/>
            </svg>
          </span>
          <span class="contact-email">email@lightfortheweary-mail.org</span>
        </li>
      </ul>
      <div class="name-box">
        <span class="name-box-top">Light for the</span>
        <span class="name-box-bottom">Weary Souls</span>
      </div>
    </div>
    <div class="card-tab">Light for the<br>Weary Souls</div>
  </section>

  <section class="card card-back" aria-label="Card back">
    <div class="card-body">
      <div class="back-signature">
        <span>Light for the<br>Weary Souls</span>
        <span class="signature-dot"></span>
      </div>
    </div>
    <div class="card-tab">Light for the<br>Weary Souls</div>
  </section>
</main>
</body>
</html>
```